Your Kid is fantastic Postcards

Tarvell State School
Attached is the one that I did up front and back – this is a postcard for the principal to send to parents about something wonderful their child had done at the school.
We want the mural photo on the front (see attached) with the window blocked out with the words from the principal put there instead. The Postcard will probably have to be long due to the photo as I tried to make one in zoomley and it left half the postcard blank we would ideally have like the A6 size. On the back will need to be as per the back of my sample one. Our website is www.tarvellss.qzedu.example cheers and thanks
School

```html
<!DOCTYPE html>
<html lang="en">
<head>
<meta charset="utf-8">
<title>Tarvell State School – Proud Postcard (Back)</title>
<link rel="stylesheet" href="https://fonts.googleapis.com/css2?family=Open+Sans:wght@300;600&family=Great+Vibes&family=Arimo:wght@700&display=swap">
<style>
  :root {
    --paper: #ffffff;
    --ink: #1a1a1a;
    --rule: #111111;
    --mural-sky: #5b93c4;
    --mural-deep: #2f5f8f;
    --mural-leaf: #8fbf7a;
    --crest-navy: #1f2a5a;
    --smile-yellow: #f4c21c;
  }
  * { box-sizing: border-box; margin: 0; padding: 0; }
  html, body { width: 1200px; height: 566px; overflow: hidden; background: var(--paper); }
  .postcard-back {
    position: relative;
    width: 1200px;
    height: 566px;
    background: var(--paper);
    color: var(--ink);
    font-family: "Open Sans", sans-serif;
    font-weight: 300;
  }
  .mural-strip {
    position: absolute;
    left: 0; top: 0;
    width: 740px; height: 40px;
    background: linear-gradient(90deg, var(--mural-deep) 0%, var(--mural-sky) 45%, rgba(91,147,196,0.55) 80%, rgba(255,255,255,0) 100%);
  }
  .mural-vine {
    position: absolute;
    left: 0; top: 36px;
    width: 90px; height: 210px;
    background: linear-gradient(180deg, rgba(143,191,122,0.85) 0%, rgba(143,191,122,0.4) 55%, rgba(255,255,255,0) 100%);
    -webkit-mask-image: linear-gradient(90deg, #000 40%, transparent 100%);
            mask-image: linear-gradient(90deg, #000 40%, transparent 100%);
  }
  .mural-bubbles {
    position: absolute;
    left: 500px; top: 36px;
    width: 200px; height: 60px;
    background: radial-gradient(ellipse at 60% 20%, rgba(91,147,196,0.35), rgba(255,255,255,0) 70%);
  }
  .greeting {
    position: absolute;
    left: 58px; top: 64px;
    font-size: 17.5px;
    line-height: 1;
  }
  .greeting .name-dots { letter-spacing: 0.5px; }
  .message-lead {
    position: absolute;
    left: 58px; top: 103px;
    font-size: 17.5px;
    line-height: 27px;
  }
  .school-name {
    position: absolute;
    left: 592px; top: 95px;
    width: 160px;
    display: flex;
    align-items: center;
    gap: 8px;
    font-family: "Open Sans", sans-serif;
    font-weight: 600;
    font-size: 15px;
    line-height: 1.2;
    color: var(--crest-navy);
  }
  .school-name .mark {
    flex: none;
    width: 14px; height: 14px;
    border-radius: 50%;
    background: var(--crest-navy);
  }
  .divider {
    position: absolute;
    left: 776px; top: 22px;
    width: 2px; height: 430px;
    background: var(--rule);
  }
  .postage-area {
    position: absolute;
    left: 1046px; top: 27px;
    width: 93px; height: 93px;
    border: 1.5px solid var(--rule);
    display: flex;
    align-items: center;
    justify-content: center;
    text-align: center;
    font-family: "Arimo", Arial, sans-serif;
    font-weight: 700;
    font-size: 16.5px;
    line-height: 1.25;
  }
  .address-lines {
    position: absolute;
    left: 860px; top: 269px;
    width: 269px;
    list-style: none;
  }
  .address-lines li {
    height: 47px;
    border-top: 2px solid var(--rule);
  }
  .sign-off {
    position: absolute;
    left: 54px; top: 472px;
    font-family: "Great Vibes", cursive;
    font-size: 25px;
    line-height: 1;
  }
  .signature {
    position: absolute;
    left: 40px; top: 508px;
    display: flex;
    align-items: center;
    gap: 10px;
    font-family: "Great Vibes", cursive;
    font-size: 25px;
  }
  .signature .smiley {
    width: 34px; height: 34px;
    border-radius: 50%;
    background: radial-gradient(circle at 40% 35%, #ffe27a, var(--smile-yellow));
  }
</style>
</head>
<body>
  <main class="postcard-back">
    <div class="mural-strip" role="img" aria-label="School mural artwork band with values banner"></div>
    <div class="mural-vine" role="img" aria-label="Mural foliage fading into the card"></div>
    <div class="mural-bubbles" role="img" aria-label="Mural speech bubbles fading out"></div>

    <p class="greeting">Dear <span class="name-dots">……………………………………………………………………</span> ,</p>
    <p class="message-lead">This postcard is to let you know<br>how proud I am that...</p>

    <div class="school-name"><span class="mark"></span><span>Tarvell State School</span></div>

    <div class="divider"></div>

    <div class="postage-area">Postage<br>Area</div>
    <ul class="address-lines">
      <li></li><li></li><li></li><li></li>
    </ul>

    <p class="sign-off">Yours in Education,</p>
    <p class="signature"><span class="smiley" role="img" aria-label="Friendly emoji sticker"></span><span>Ms Orvel</span></p>
  </main>
</body>
</html>
```